Business Card Design Project

I need a business card designed from scratch. I have an existing logo that I can upload in Illustrator for modification or redesign.

The Company is called Query Lanterns http://querylanterns.com.au and we provide Search Engine Optimization services to Australian businesses. The current logo signifies an increase in visitors, profits etc...

There are no restrictions as to the redesign - colours, style etc are all open to change.

Cards will be full colour and one sided printed at http://www.cardmoxel.com.au so check their requirements for file format and sizes etc.

I will expect all original files upon completion of project.

Target Market(s)

Any business with a web site looking to improve their search engine rankings

Industry/Entity Type

Business

Requirements
Must have
• I like modern, sleek designs. Clean, not fussy, uncluttered.

```html
<!DOCTYPE html>
<html lang="en">
<head>
<meta charset="utf-8">
<title>Query Lanterns – Business Card</title>
<link href="https://fonts.googleapis.com/css2?family=Montserrat:wght@700;800&family=Open+Sans:wght@600;700&display=swap" rel="stylesheet">
<style>
  :root {
    --stage: #e9e9ea;
    --card: #ffffff;
    --card-edge: #f1f1f3;
    --brand-blue: #1b6db3;
    --deep-blue: #1c3f7c;
    --accent-yellow: #f1c203;
    --icon-blue: #2a66b0;
  }
  * { box-sizing: border-box; margin: 0; padding: 0; }
  html, body {
    width: 1187px;
    height: 1200px;
    overflow: hidden;
    background: var(--stage);
  }
  .canvas {
    position: relative;
    width: 1187px;
    height: 1200px;
  }
  .card {
    position: absolute;
    left: 220px;
    width: 729px;
    height: 471px;
    background: linear-gradient(135deg, var(--card) 55%, var(--card-edge) 100%);
    box-shadow: 0 2px 10px rgba(0, 0, 0, 0.12);
  }
  .card--front { top: 73px; }
  .card--back { top: 643px; }

  .wordmark {
    position: absolute;
    display: flex;
    align-items: center;
    font-family: "Montserrat", sans-serif;
    font-weight: 800;
    color: var(--brand-blue);
    white-space: nowrap;
  }
  .wordmark__dot {
    border-radius: 50%;
    background: var(--accent-yellow);
    flex: none;
  }
  .card--front .wordmark {
    left: 40px;
    top: 180px;
    font-size: 68px;
    letter-spacing: -1px;
    gap: 22px;
  }
  .card--front .wordmark__dot { width: 44px; height: 44px; }

  .card--back .wordmark {
    left: 26px;
    top: 342px;
    font-size: 24px;
    gap: 10px;
  }
  .card--back .wordmark__dot { width: 18px; height: 18px; }

  .divider {
    position: absolute;
    left: 321px;
    top: 297px;
    width: 4px;
    height: 128px;
    background: var(--accent-yellow);
  }
  .contact {
    position: absolute;
    left: 364px;
    top: 296px;
    font-family: "Open Sans", sans-serif;
  }
  .contact__name {
    margin-left: 20px;
    font-size: 19px;
    font-weight: 700;
    color: var(--brand-blue);
  }
  .contact__role {
    margin-left: 24px;
    margin-top: 2px;
    font-size: 16px;
    font-weight: 700;
    color: var(--brand-blue);
  }
  .contact__list {
    list-style: none;
    margin-top: 10px;
  }
  .contact__item {
    display: flex;
    align-items: center;
    gap: 10px;
    height: 27px;
    font-size: 13px;
    font-weight: 700;
    color: var(--accent-yellow);
  }
  .contact__icon {
    width: 20px;
    height: 20px;
    fill: none;
    stroke: var(--icon-blue);
    stroke-width: 2;
  }
  .contact__icon--solid { fill: var(--icon-blue); stroke: none; }
</style>
</head>
<body>
<main class="canvas">
  <section class="card card--front" aria-label="Card front">
    <div class="wordmark">
      <span class="wordmark__dot"></span>
      <span class="wordmark__name">Query Lanterns</span>
    </div>
  </section>

  <section class="card card--back" aria-label="Card back">
    <div class="wordmark">
      <span class="wordmark__dot"></span>
      <span class="wordmark__name">Query Lanterns</span>
    </div>
    <div class="divider"></div>
    <div class="contact">
      <p class="contact__name">Dale Morrow</p>
      <p class="contact__role">Internet Marketing Consultant</p>
      <ul class="contact__list">
        <li class="contact__item">
          <svg class="contact__icon" viewBox="0 0 20 20" aria-hidden="true">
            <circle cx="10" cy="10" r="8"/>
            <ellipse cx="10" cy="10" rx="3.5" ry="8"/>
            <line x1="2" y1="10" x2="18" y2="10"/>
            <line x1="3.5" y1="6" x2="16.5" y2="6"/>
            <line x1="3.5" y1="14" x2="16.5" y2="14"/>
          </svg>
          <span>www.querylanterns.com.au</span>
        </li>
        <li class="contact__item">
          <svg class="contact__icon" viewBox="0 0 20 20" aria-hidden="true">
            <rect x="2" y="5" width="16" height="11" rx="1"/>
            <polyline points="2,5 10,11.5 18,5"/>
          </svg>
          <span>dale@querylanterns.com.au</span>
        </li>
        <li class="contact__item">
          <svg class="contact__icon contact__icon--solid" viewBox="0 0 20 20" aria-hidden="true">
            <path d="M3 7c0-2 3-3.5 7-3.5S17 5 17 7v1.5h-3.5V7h-7v1.5H3z"/>
            <path d="M5 10h10l1.5 7h-13z"/>
          </svg>
          <span>1300 555 014</span>
        </li>
      </ul>
    </div>
  </section>
</main>
</body>
</html>
```